TLK Electricial Contracting Services

Hi guys, after a design for my small electrical company, have logo design files to be incorporated into the layout, the basic concept is electrical contracting services for residential, commercial, industrial & data services, image is clean clear and strong,

Card format is to have a nice clean logo on front,with maybe the Residential – commercial – industrial - data, followed with licensed & insured, followed by contact details on backside of the card.

Target Market(s)

Residential, commercial, industrial sectors.

Industry/Entity Type

Electrical

Contact Information for Business Card

TLK logo,
Residential – commercial – industrial - data
REC: 61307
Email: tlk@vornamail.net.au
Phone: 0487 352 019

Requirements
Must have
• Clean & strong design.
Nice to have
• If possible, I would like the logo colours inverted so the text is orange and the background is black on the front of the card, then the backside of the card be the reverse colour
Should not have
• No Sparks, lightning bolts,

```html
<!DOCTYPE html>
<html lang="en">
<head>
<meta charset="utf-8">
<title>TLK Electricial Contracting Services – Business Card</title>
<link rel="stylesheet" href="https://fonts.googleapis.com/css2?family=Lato:wght@400;700;900&display=swap">
<style>
  :root {
    --orange: #f47e2a;
    --orange-deep: #e86f1c;
    --white: #ffffff;
    --paper: #f2f2f2;
    --ink: #111111;
    --muted-on-orange: #fbd2b2;
    --backdrop: #e4e1dc;
  }
  * { box-sizing: border-box; margin: 0; padding: 0; }
  html, body { width: 1200px; height: 900px; overflow: hidden; }
  body {
    background: var(--backdrop);
    font-family: "Lato", sans-serif;
    position: relative;
  }
  .card {
    position: absolute;
    width: 525px;
    height: 300px;
    border-radius: 4px;
    overflow: hidden;
    box-shadow: 0 10px 30px rgba(0,0,0,.18);
  }
  .card--front {
    left: 50px; top: 300px;
    background: radial-gradient(ellipse at 50% 45%, var(--orange) 0%, var(--orange-deep) 100%);
    display: flex; align-items: center; justify-content: center;
  }
  .card--back {
    left: 625px; top: 300px;
    background: var(--orange);
  }
  .wordmark { display: flex; flex-direction: column; align-items: flex-end; font-weight: 900; }
  .wordmark__name { font-size: 92px; line-height: .9; letter-spacing: 2px; }
  .wordmark__tag { font-size: 17px; letter-spacing: .3px; margin-top: 4px; }
  .card--front .wordmark { color: var(--ink); }
  .card--back .wordmark { color: var(--orange); }
  .card--back .wordmark__name { font-size: 80px; }
  .card--back .wordmark__tag { font-size: 15px; }
  .back__top {
    height: 138px;
    background: linear-gradient(180deg, var(--white) 0%, var(--paper) 100%);
    display: flex; align-items: center; justify-content: center;
    padding-top: 10px;
  }
  .back__bottom {
    height: 162px;
    display: flex; justify-content: space-between;
    padding: 22px 34px 0 40px;
    color: var(--white);
  }
  .person { text-align: right; }
  .person__name { font-size: 24px; font-weight: 400; line-height: 1.1; }
  .person__role { font-size: 15px; color: var(--muted-on-orange); margin-bottom: 12px; }
  .person__address { font-size: 18px; line-height: 1.3; }
  .contacts { list-style: none; font-size: 14px; padding-top: 2px; }
  .contacts li { display: flex; align-items: center; gap: 8px; height: 24px; }
  .contacts svg { width: 16px; height: 16px; flex: none; }
</style>
</head>
<body>
  <section class="card card--front" aria-label="Card front">
    <div class="wordmark">
      <span class="wordmark__name">TLK</span>
      <span class="wordmark__tag">Tarlek Electrical</span>
    </div>
  </section>

  <section class="card card--back" aria-label="Card back">
    <div class="back__top">
      <div class="wordmark">
        <span class="wordmark__name">TLK</span>
        <span class="wordmark__tag">Tarlek Electrical</span>
      </div>
    </div>
    <div class="back__bottom">
      <div class="person">
        <p class="person__name">Liam Carter</p>
        <p class="person__role">Managing Director</p>
        <p class="person__address">1234, Address GoesHere<br>Country, 12345</p>
      </div>
      <ul class="contacts">
        <li>
          <svg viewBox="0 0 16 16" aria-hidden="true"><rect width="16" height="16" rx="3" fill="#fff"/><path d="M5 4c-1 1-1 2 0 4s3 4 5 4 2-1 2-1l-2-2-1 1c-1-.5-2-1.5-2.5-2.5l1-1-2-2z" fill="#f47e2a"/></svg>
          <span>123-456-7890</span>
        </li>
        <li>
          <svg viewBox="0 0 16 16" aria-hidden="true"><rect width="16" height="16" rx="3" fill="#fff"/><rect x="4" y="3" width="8" height="4" fill="#f47e2a"/><rect x="3" y="7" width="10" height="5" rx="1" fill="#f47e2a"/><rect x="5" y="10" width="6" height="3" fill="#fff"/></svg>
          <span>123-456-7890</span>
        </li>
        <li>
          <svg viewBox="0 0 16 16" aria-hidden="true"><rect width="16" height="16" rx="3" fill="#fff"/><rect x="3" y="4.5" width="10" height="7" fill="#f47e2a"/><path d="M3 4.5l5 4 5-4" fill="none" stroke="#fff" stroke-width="1.2"/></svg>
          <span>info@youremail.com</span>
        </li>
        <li>
          <svg viewBox="0 0 16 16" aria-hidden="true"><rect width="16" height="16" rx="3" fill="#fff"/><path d="M7 9l2-2M6 7.5l-1.5 1.5a1.8 1.8 0 002.5 2.5L8.5 10M10 8.5l1.5-1.5a1.8 1.8 0 00-2.5-2.5L7.5 6" fill="none" stroke="#f47e2a" stroke-width="1.4" stroke-linecap="round"/></svg>
          <span>www.yourweb.com</span>
        </li>
      </ul>
    </div>
  </section>
</body>
</html>
```